Harborlight Amusement Collective (HAC)

We need a business card design for Harborlight Amusement Collective. Modern and sleek looking, with all critical information. Open to single or double sided designs, if double sided info needs to be all on one side. The main Logo is Harborlight Amusement collective and must be on the card. The other three logos are for the brands that fall under the group, they might be good on the back.

Industry/Entity Type

Business

```html
<!DOCTYPE html>
<html lang="en">
<head>
<meta charset="utf-8">
<title>Harborlight Amusement Collective – Business Card</title>
<link rel="stylesheet" href="https://fonts.googleapis.com/css2?family=Montserrat:wght@400;500;600;700&display=swap">
<style>
  :root {
    --blue: #2757a0;
    --green: #8cb033;
    --ink: #222;
    --paper: #ffffff;
    --backdrop: #d9d9d9;
  }
  * { box-sizing: border-box; margin: 0; padding: 0; }
  html, body { width: 1200px; height: 852px; overflow: hidden; }
  body {
    background: var(--backdrop);
    font-family: "Montserrat", sans-serif;
    color: var(--ink);
    position: relative;
  }
  .card {
    position: absolute;
    top: 281px;
    width: 500px;
    height: 290px;
    background: var(--paper);
    border-radius: 18px;
    overflow: hidden;
    box-shadow: 0 6px 16px rgba(0,0,0,.18);
  }
  .card--front { left: 80px; }
  .card--back { left: 620px; }

  .wordmark {
    display: flex;
    align-items: center;
    gap: 10px;
    color: var(--blue);
    font-weight: 700;
    text-transform: uppercase;
    font-size: 17px;
    line-height: 1.15;
  }
  .wordmark__square {
    width: 38px; height: 38px;
    background: var(--blue);
    flex: none;
  }

  /* Front */
  .card--front .wordmark { position: absolute; left: 70px; top: 48px; width: 360px; }
  .rule { position: absolute; height: 2px; }
  .rule--top { left: 60px; right: 60px; top: 118px; background: var(--green); }
  .rule--bottom { left: 60px; right: 60px; top: 206px; background: var(--green); }
  .brands-label {
    position: absolute; top: 128px; width: 100%;
    text-align: center; font-size: 12px; color: #555;
  }
  .brands {
    position: absolute; top: 152px; left: 30px; right: 30px;
    display: flex; justify-content: space-between; align-items: center;
  }
  .brand {
    display: flex; align-items: center; gap: 6px;
    font-size: 15px; font-weight: 700; color: var(--blue);
  }
  .brand__dot { width: 14px; height: 14px; border-radius: 50%; background: var(--green); }
  .brand-sep { width: 1px; height: 30px; background: #999; }
  .card--front .site {
    position: absolute; top: 218px; width: 100%;
    text-align: center; font-size: 12.5px; color: #333;
  }
  .site b { color: var(--blue); font-weight: 500; }

  /* Back */
  .wave { position: absolute; inset: 0; }
  .person {
    position: absolute; right: 26px; top: 12px; text-align: right; color: #fff;
  }
  .person__name { font-size: 17px; font-weight: 700; }
  .person__title { font-size: 11px; font-weight: 400; margin-top: 2px; }
  .card--back .wordmark {
    position: absolute; left: 26px; top: 188px; width: 210px; font-size: 12px; gap: 8px;
  }
  .card--back .wordmark__square { width: 30px; height: 30px; }
  .address {
    position: absolute; left: 26px; bottom: 20px;
    font-size: 12.5px; line-height: 1.5;
  }
  .contacts {
    position: absolute; right: 22px; top: 116px;
    list-style: none; text-align: right; font-size: 11.5px; line-height: 1.75;
  }
  .contacts li { display: flex; justify-content: flex-end; align-items: center; gap: 6px; }
  .contacts svg { width: 11px; height: 11px; fill: var(--blue); flex: none; }
</style>
</head>
<body>

<section class="card card--front" aria-label="Card front">
  <div class="wordmark"><span class="wordmark__square"></span><span>Harborlight Amusement Collective</span></div>
  <div class="rule rule--top"></div>
  <p class="brands-label">Our Brands</p>
  <div class="brands">
    <span class="brand"><span class="brand__dot"></span>HarborTix</span>
    <span class="brand-sep"></span>
    <span class="brand"><span class="brand__dot"></span>Bleacherline Hospitality</span>
    <span class="brand-sep"></span>
    <span class="brand"><span class="brand__dot"></span>gatepass</span>
  </div>
  <div class="rule rule--bottom"></div>
  <p class="site">www.<b>harborlightcollective</b>.com</p>
</section>

<section class="card card--back" aria-label="Card back">
  <svg class="wave" viewBox="0 0 500 290" preserveAspectRatio="none">
    <path fill="var(--blue)" d="M0,40 C60,30 110,15 150,0 H500 V55 C400,58 330,70 260,92 C180,118 80,115 0,100 Z"/>
    <path fill="var(--green)" d="M500,62 C400,65 330,77 260,99 C180,125 80,122 0,108 V116 C80,132 180,134 260,107 C330,84 400,72 500,70 Z"/>
  </svg>
  <div class="person">
    <p class="person__name">Jordan Avery Lane</p>
    <p class="person__title">Managing Director</p>
  </div>
  <div class="wordmark"><span class="wordmark__square"></span><span>Harborlight Amusement Collective</span></div>
  <ul class="contacts">
    <li>555.014.2870
      <svg viewBox="0 0 24 24"><path d="M6.6 10.8a15 15 0 0 0 6.6 6.6l2.2-2.2a1 1 0 0 1 1-.25 11.4 11.4 0 0 0 3.6.57 1 1 0 0 1 1 1V20a1 1 0 0 1-1 1A17 17 0 0 1 3 4a1 1 0 0 1 1-1h3.5a1 1 0 0 1 1 1c0 1.25.2 2.45.57 3.6a1 1 0 0 1-.25 1z"/></svg></li>
    <li>jordan@harborlightcollective.com
      <svg viewBox="0 0 24 24"><path d="M2 5h20v14H2z M2 5l10 8 10-8" fill="var(--blue)" stroke="#fff" stroke-width="1.5"/></svg></li>
    <li>www.harborlightcollective.com
      <svg viewBox="0 0 24 24"><circle cx="12" cy="12" r="10"/><path d="M2 12h20M12 2c3 3 3 17 0 20M12 2c-3 3-3 17 0 20" stroke="#fff" stroke-width="1.4" fill="none"/></svg></li>
  </ul>
  <p class="address">48 Quayside Row,<br>Port Ellery, US 904417</p>
</section>

</body>
</html>
```